Bold, Modern, Clean "Kestrelwaymassage.com" website

Why we stand out?
We are a male and female mobile massage team. Our names are Paul and Lina. 
Kestrel Way is a Seattle based mobile massage service. Our massage is offered to the community with a goal of facilitating balance within each individual. We specialize in integrated Pain management, and sports/medical massage therapy. Every client's first assessment is attended by our male and female massage therapist team. Depending on the goals identified for an individual determines which therapist will be assigned to provide treatment, if not both.

Our passion...
Here at Kestrel Way, we have a great passion for Postural Resoration and how it is integrated into an individual's Massage treatment. We pride ourselves in being natural facilitators of healing, which takes the ego of the therapist out of the client's healing process. We strive to deliver the best massage possible by including modalities such as Neuromuscular, Myofascial release, spontaneous muscle release, postural restoration, orthopedic, and medical massage.

Our education...

We are both Graduates of Venmora, school of massage therapy. We have continuing education in medical massage, myofacial release, trigger point therapy, postural restoration, anatomy, and spontaneous muscle release. Lina is also a Certified Yoga Instructor, which amplifies her experience with flexibility and strength as it pertains to each individual. Paul's passion is Massage, stretching, and strength training to encourage postural restoration and realignment.

Our rates-

Our rates are $75/ 60 minutes, $95/ 90 minutes, and $120/ 120 minutes.

Education-
Both Lina and I worked as behavioral health professionals that specialized in life skills mentoring for youth who had experienced different types of trauma. This led us both to want to help others in a different environment, where individuals can be empowered to take responsibility over their own healing. To us, massage is a type of manipulation physical therapy, that encourages healing on many levels.

Advice to any massage client-
The most important thing to 'us', as Licenced providers is to get you on to our table to show you our skills. But a good therapist never forgets that it's not about what we do for you, but what we can facilitate for you. Your health and healing has nothing to do with us. It is yours, not ours. Identify what your goals are with any Therapist, and know what the end looks like. Progress should be tangible, such as range of motion, and decreased pain.

Lina and Paul at Kestrel Way are awesome! I recently had open heart surgery, and Lina worked on me to increase my range of motion while helping with the pinched nerve from my arm being in the same position for so long during my surgery. My wife drives a lot for work, and Paul has helped decrease her neck and lower back pain immensely. They are seriously the best therapists I have ever worked with. I would recommend them to anyone who needs anything from stress relief to a medical massage treatment. They are professional, up beat, easy going, and always on time. And, I love that they meet us where ever we like! We did a staycation recently, where they came to our hotel to give us relaxation massages. Although usually they come to our home, where we focus on pain related issues. We will continue to work with them for a long, long time.

Target Market(s)

Mobile massage therapy clients

Industry/Entity Type

Massage Therapy

Coding

Coded - Design and coding required

Number of Pages Required

1 page

Font styles to use
Serif
Sans Serif

Requirements
Must have
• Please add or remove any information that would help the presentation of our website. Our logo is posted below, please include into the website.
• Please include a contact field that includes, kestrelwaymassage@fernmail.net,
• (206) 555-0148
• We have also included our own stock photos, as well as a photo of Paul and Lina. Please include a cropped photo of both massage therapists.

```html
<!DOCTYPE html>
<html lang="en">
<head>
<meta charset="utf-8">
<title>Kestrel Way Mobile Massage</title>
<link href="https://fonts.googleapis.com/css2?family=Lato:wght@300;400;700;900&family=Dancing+Script:wght@500&display=swap" rel="stylesheet">
<style>
:root{
  --black:#0d0d0d;
  --dark:#141414;
  --charcoal:#2a2a2a;
  --teal:#1fd1b4;
  --teal-deep:#0e9f8c;
  --teal-bar:#0f6f63;
  --blue:#1f8fd8;
  --navy:#1a2c9e;
  --text:#444;
  --white:#fff;
  --light:#f3f3f3;
}
*{box-sizing:border-box;margin:0;padding:0}
html,body{width:1200px;height:3041px;overflow:hidden}
body{position:relative;font-family:"Lato",sans-serif;color:var(--text);background:var(--white)}
.abs{position:absolute}

/* header */
.topbar{left:0;top:0;width:1200px;height:97px;background:var(--black)}
.contact-item{top:36px;display:flex;align-items:center;gap:10px;color:var(--white);font-size:15px}
.contact-icon{width:26px;height:26px;border-radius:50%;background:var(--navy);display:flex;align-items:center;justify-content:center}
.navbar{left:0;top:97px;width:1200px;height:45px;background:linear-gradient(90deg,var(--teal-deep),var(--teal) 40%,var(--teal-deep))}
.nav-link{top:97px;height:45px;line-height:45px;color:var(--white);font-size:13px;font-weight:700;text-transform:uppercase;text-align:center;transform:translateX(-50%);white-space:nowrap}
.nav-home{left:324px;top:97px;width:98px;height:45px;background:var(--black);color:var(--white);font-size:13px;font-weight:700;text-align:center;line-height:45px}
.nav-sep{top:110px;width:1px;height:19px;background:rgba(255,255,255,.45)}
.brand{left:59px;top:19px;width:194px;height:194px;border-radius:50%;background:radial-gradient(circle at 40% 35%,#3aa6ea,var(--blue) 60%,#1461b0);border:6px solid var(--white);display:flex;align-items:center;justify-content:center;z-index:3}
.brand span{color:var(--white);font-weight:900;font-size:30px;text-align:center;line-height:1.05;text-transform:uppercase}

/* hero */
.hero{left:0;top:142px;width:1200px;height:541px;background:
  radial-gradient(ellipse 140px 110px at 580px 520px,rgba(255,236,190,.75),transparent 70%),
  radial-gradient(ellipse 420px 260px at 930px 330px,#f2dcc6,transparent 70%),
  radial-gradient(ellipse 360px 150px at 560px 80px,#f6e7dc,transparent 70%),
  radial-gradient(ellipse 260px 260px at 150px 300px,#2e1c12,transparent 75%),
  linear-gradient(100deg,#3a2416 0%,#6b4328 22%,#a76c45 42%,#c99572 62%,#e4c6ab 82%,#d3b49a 100%)}
.hero-text{left:101px;top:472px;font-family:"Dancing Script",cursive;font-size:31px;line-height:44px;color:var(--white);width:600px;text-shadow:0 1px 3px rgba(0,0,0,.4)}
.hero-arrow{top:628px}

/* welcome */
.section-title{font-weight:300;font-size:31px;color:var(--text)}
.card-photo{top:805px;width:299px;height:154px;border:1px solid #ddd}
.card-title{top:980px;width:299px;text-align:center;color:var(--blue);font-size:20px}
.card-text{top:1024px;width:299px;text-align:center;font-size:12.5px;line-height:21px;color:var(--text)}
.btn{display:block;width:115px;height:34px;line-height:34px;background:var(--navy);color:var(--white);font-size:13px;font-weight:700;text-align:center;box-shadow:0 2px 4px rgba(0,0,0,.3)}
.booking{left:792px;top:744px;width:309px;height:404px;background:var(--white);box-shadow:0 0 8px rgba(0,0,0,.2)}
.booking h3{position:absolute;left:50px;top:17px;font-weight:300;font-size:21px;color:var(--text)}
.field{position:absolute;left:19px;width:269px;border:1px dashed #ccc;font-size:11px;color:#555}
.field .ico{position:absolute;left:0;top:0;width:32px;height:100%;border-right:1px dashed #ccc}
.field .ico svg{position:absolute;left:9px;top:12px}
.field span{position:absolute;left:42px;top:13px}

/* services */
.services{left:0;top:1206px;width:1200px;height:456px;background:var(--dark)}
.service-disc{top:1326px;width:194px;height:194px;border-radius:50%;border:7px solid var(--teal);background:
  radial-gradient(circle at 30% 30%,rgba(120,220,245,.7),transparent 35%),
  radial-gradient(circle at 70% 75%,rgba(10,60,120,.7),transparent 45%),
  radial-gradient(circle at 45% 40%,#33b8e4,#1573b8 65%,#0c4f8a);box-shadow:0 12px 14px rgba(0,0,0,.7);display:flex;align-items:center;justify-content:center}
.service-label{top:1554px;width:260px;text-align:center;color:#e8e8e8;font-size:20px;line-height:27px;transform:translateX(-50%)}

/* advice */
.advice{left:0;top:1662px;width:1200px;height:355px;background:
  radial-gradient(ellipse 380px 260px at 1000px 150px,rgba(220,170,140,.55),transparent 70%),
  radial-gradient(ellipse 300px 200px at 150px 120px,rgba(190,120,80,.45),transparent 70%),
  linear-gradient(100deg,#2c1c14 0%,#5a3a28 40%,#6e4836 65%,#3a2418 100%)}
.advice-text{left:116px;top:1864px;width:968px;text-align:center;color:#f1f1f1;font-size:14.5px;line-height:23px;letter-spacing:.1px}
.ring-icon{width:72px;height:72px;border-radius:50%;border:2px solid var(--white);display:flex;align-items:center;justify-content:center}

/* testimonials */
.testimonials{left:0;top:2017px;width:1200px;height:375px;background:var(--light)}
.testimonial-text{left:138px;top:2132px;width:924px;text-align:center;font-size:13.5px;line-height:22px;color:#333}
.quote-mark{font-size:150px;font-weight:900;color:#d8d8d8;line-height:1}

/* rates */
.rates{left:0;top:2392px;width:1200px;height:604px;background:linear-gradient(180deg,var(--teal) 0%,#17c0a6 50%,var(--teal-deep) 100%)}
.rate-bar{left:124px;top:2635px;width:954px;height:43px;border-radius:22px;background:var(--teal-bar);display:flex}
.rate{flex:1;display:flex;align-items:center;justify-content:center;gap:12px;color:var(--white);font-size:14px;font-weight:700;border-right:1px solid rgba(255,255,255,.3)}
.rate:last-child{border-right:none}
.rate .pair{display:flex;align-items:center;gap:8px}

/* footer */
.footer-logo{left:161px;top:2736px;width:180px;height:180px;border-radius:50%;background:radial-gradient(circle at 40% 40%,#f2f2f2,#bdbdbd);border:5px solid #e6e6e6;display:flex;align-items:center;justify-content:center}
.footer-logo span{color:#3a3a3a;font-weight:900;font-size:27px;text-transform:uppercase;text-align:center;line-height:1.05}
.footer-link{top:2936px;color:#eaeaea;font-size:13.5px;text-transform:uppercase;transform:translateX(-50%);white-space:nowrap}
.footer-sep{top:2936px;width:1px;height:18px;background:#777}
.bottombar{left:0;top:2996px;width:1200px;height:45px;background:var(--teal)}
.copyright{left:99px;top:3011px;font-size:12px;color:#123}
.social-dot{top:3014px;width:12px;height:12px;border-radius:50%;background:var(--charcoal)}
</style>
</head>
<body>

<!-- header -->
<div class="abs topbar"></div>
<div class="abs contact-item" style="left:706px">
  <span class="contact-icon"><svg width="13" height="13" viewBox="0 0 24 24"><path fill="#fff" d="M6.6 10.8a15 15 0 0 0 6.6 6.6l2.2-2.2c.3-.3.7-.4 1-.2 1.1.4 2.3.6 3.6.6.6 0 1 .4 1 1V20c0 .6-.4 1-1 1A17 17 0 0 1 3 4c0-.6.4-1 1-1h3.5c.6 0 1 .4 1 1 0 1.3.2 2.5.6 3.6.1.3 0 .7-.2 1z"/></svg></span>
  (206) 555-0148
</div>
<div class="abs contact-item" style="left:870px">
  <span class="contact-icon"><svg width="13" height="11" viewBox="0 0 24 18"><path fill="#fff" d="M0 0h24v18H0z"/><path d="M0 0l12 9 12-9" stroke="#1a2c9e" stroke-width="2" fill="none"/></svg></span>
  kestrelwaymassage@fernmail.net
</div>

<div class="abs navbar"></div>
<div class="abs nav-home">HOME</div>
<div class="abs nav-link" style="left:541px">Why we stand out?</div>
<div class="abs nav-sep" style="left:635px"></div>
<div class="abs nav-link" style="left:734px">Our Passion</div>
<div class="abs nav-sep" style="left:815px"></div>
<div class="abs nav-link" style="left:894px">Education</div>
<div class="abs nav-sep" style="left:972px"></div>
<div class="abs nav-link" style="left:1054px">Contact Us</div>

<div class="abs brand"><span>Kestrel<br>Way</span></div>

<!-- hero -->
<div class="abs hero" role="img" aria-label="Therapist's hands giving a back massage to a relaxed client beside a lit candle and spa stones"></div>
<div class="abs hero-text">We Are A Seattle Based Mobile Massage Service Specialize In Integrated Pain Management, And Sports/medical Massage Therapy.</div>
<svg class="abs hero-arrow" style="left:98px" width="14" height="34" viewBox="0 0 14 34"><path d="M12 2L2 17l10 15" stroke="#fff" stroke-width="2" fill="none"/></svg>
<svg class="abs hero-arrow" style="left:144px" width="14" height="34" viewBox="0 0 14 34"><path d="M2 2l10 15L2 32" stroke="#fff" stroke-width="2" fill="none"/></svg>

<!-- welcome -->
<svg class="abs" style="left:98px;top:736px" width="36" height="30" viewBox="0 0 36 30"><rect x="2" y="22" width="32" height="5" fill="#1fd1b4"/><circle cx="10" cy="8" r="5" fill="#1fd1b4"/><path d="M14 18h16" stroke="#1fd1b4" stroke-width="5"/></svg>
<div class="abs section-title" style="left:142px;top:734px">Welcome to Kestrel Way Mobile Massage</div>

<div class="abs card-photo" style="left:111px;background:linear-gradient(120deg,#bfc7cc,#e6d2c0 50%,#8a6a58)" role="img" aria-label="Therapist using a percussion massage device on a client's back"></div>
<div class="abs card-title" style="left:111px">Our Passion</div>
<div class="abs card-text" style="left:111px">Here at Kestrel Way, we have a great passion for<br>Postural Resoration and how it is integrated into an<br>individual's Massage treatment...</div>
<a class="abs btn" style="left:203px;top:1105px">Read More</a>

<div class="abs card-photo" style="left:448px;background:linear-gradient(90deg,#c9a88e,#f0e4d8 50%,#c49a7c)" role="img" aria-label="Portrait of the two massage therapists, Paul and Lina"></div>
<div class="abs card-title" style="left:448px">Our Education</div>
<div class="abs card-text" style="left:448px">We are both Graduates of Venmora, school of<br>massage therapy. We have continuing education in<br>medical massage, myofacial release...</div>
<a class="abs btn" style="left:540px;top:1105px">Read More</a>

<div class="abs booking">
  <svg style="position:absolute;left:20px;top:22px" width="20" height="20" viewBox="0 0 20 20"><rect x="1" y="3" width="14" height="16" fill="none" stroke="#1fd1b4" stroke-width="2"/><path d="M8 12l9-10" stroke="#1fd1b4" stroke-width="2"/></svg>
  <h3>Book An Appointment</h3>
  <div class="field" style="top:60px;height:41px"><div class="ico"><svg width="13" height="13" viewBox="0 0 12 12"><circle cx="6" cy="4" r="3" fill="#555"/><path d="M0 12c0-4 12-4 12 0z" fill="#555"/></svg></div><span>Name</span></div>
  <div class="field" style="top:109px;height:43px"><div class="ico"><svg width="13" height="10" viewBox="0 0 12 9"><rect width="12" height="9" fill="#555"/><path d="M0 0l6 5 6-5" stroke="#fff" fill="none"/></svg></div><span>Email</span></div>
  <div class="field" style="top:160px;height:43px"><div class="ico"><svg width="13" height="13" viewBox="0 0 24 24"><path fill="#555" d="M6.6 10.8a15 15 0 0 0 6.6 6.6l2.2-2.2c.3-.3.7-.4 1-.2 1.1.4 2.3.6 3.6.6.6 0 1 .4 1 1V20c0 .6-.4 1-1 1A17 17 0 0 1 3 4c0-.6.4-1 1-1h3.5c.6 0 1 .4 1 1 0 1.3.2 2.5.6 3.6.1.3 0 .7-.2 1z"/></svg></div><span>Phone</span></div>
  <div class="field" style="top:211px;height:125px"><div class="ico"><svg width="13" height="13" viewBox="0 0 12 12"><rect x="0.5" y="1.5" width="9" height="10" fill="none" stroke="#555"/><path d="M5 7l6-6" stroke="#555"/></svg></div><span>Message</span></div>
  <a class="btn" style="position:absolute;left:21px;top:347px;width:113px;height:36px;line-height:36px">Book Now</a>
</div>

<!-- services -->
<div class="abs services"></div>
<svg class="abs" style="left:495px;top:1256px" width="28" height="28" viewBox="0 0 28 28"><circle cx="14" cy="14" r="11" fill="none" stroke="#1fd1b4" stroke-width="3"/><circle cx="14" cy="14" r="4" fill="#1fd1b4"/></svg>
<div class="abs" style="left:530px;top:1253px;font-size:30px;font-weight:300;color:#fff">Our Services</div>

<div class="abs service-disc" style="left:203px">
  <svg width="92" height="80" viewBox="0 0 92 80"><path d="M46 74C20 56 6 42 6 25 6 13 15 5 26 5c8 0 15 5 20 12 5-7 12-12 20-12 11 0 20 8 20 20 0 17-14 31-40 49z" fill="#fff"/><path d="M14 38h18l6-12 8 24 7-16 5 4h20" stroke="#1573b8" stroke-width="5" fill="none" stroke-linejoin="round" stroke-linecap="round"/></svg>
</div>
<div class="abs service-disc" style="left:503px">
  <svg width="80" height="90" viewBox="0 0 80 90"><rect x="32" y="2" width="16" height="9" rx="2" fill="#fff"/><rect x="37" y="9" width="6" height="8" fill="#fff"/><path d="M64 18l7 7" stroke="#fff" stroke-width="6" stroke-linecap="round"/><circle cx="40" cy="52" r="34" fill="#fff"/><circle cx="40" cy="52" r="27" fill="none" stroke="#1573b8" stroke-width="3"/><path d="M40 32v20l13 9" stroke="#1573b8" stroke-width="6" fill="none" stroke-linecap="round"/></svg>
</div>
<div class="abs service-disc" style="left:801px">
  <svg width="76" height="92" viewBox="0 0 76 92"><rect x="26" y="2" width="24" height="9" rx="2" fill="#fff"/><path d="M30 11h16v20l24 40c4 8 0 17-9 17H15c-9 0-13-9-9-17l24-40z" fill="#fff"/><path d="M14 66h48l5 9c2 4 0 8-5 8H14c-5 0-7-4-5-8z" fill="#1573b8" opacity=".35"/><path d="M34 52h8M38 48v8" stroke="#1573b8" stroke-width="4" stroke-linecap="round"/></svg>
</div>
<div class="abs service-label" style="left:300px">Integrated<br>Pain management</div>
<div class="abs service-label" style="left:600px">Sports<br>Massage Therapy</div>
<div class="abs service-label" style="left:898px">Medical<br>Massage Therapy</div>

<!-- advice -->
<div class="abs advice" role="img" aria-label="Woman relaxing face down on a massage towel"></div>
<div class="abs ring-icon" style="left:564px;top:1701px"><svg width="36" height="36" viewBox="0 0 36 36"><circle cx="14" cy="12" r="7" fill="#fff"/><path d="M2 34c0-10 24-10 24 0z" fill="#fff"/><circle cx="27" cy="10" r="7" fill="none" stroke="#fff" stroke-width="2"/><path d="M27 7v5" stroke="#fff" stroke-width="2"/></svg></div>
<div class="abs" style="left:0;top:1797px;width:1200px;text-align:center;font-size:30px;color:#fff;font-weight:400">Advice To Any Massage Client</div>
<div class="abs advice-text">The Most Important Thing To 'us', As Licenced Providers Is To Get You On To Our Table To Show You Our Skills, But A Good Therapist Never Forgets That It's Not About What We Do For You, But What We Can Facilitate For You. Your Health And Healing Has Nothing To Do With Us. It Is Yours, Not Ours. Identify What Your Goals Are With Any Therapist, And Know What The End Looks Like. Progress Should Be Tangible, Such As Range Of Motion, And Decreased Pain.</div>

<!-- testimonials -->
<div class="abs testimonials"></div>
<div class="abs quote-mark" style="left:32px;top:2140px">&ldquo;</div>
<div class="abs quote-mark" style="left:1100px;top:2170px">&rdquo;</div>
<svg class="abs" style="left:444px;top:2072px" width="34" height="34" viewBox="0 0 34 34"><circle cx="18" cy="20" r="12" fill="#1fd1b4"/><circle cx="8" cy="6" r="4" fill="#1fd1b4"/></svg>
<div class="abs" style="left:488px;top:2069px;font-size:29px;font-weight:300;color:#444">Clients Testimonials</div>
<div class="abs testimonial-text">Lina and Paul at Kestrel Way are awesome! I recently had open heart surgery, and Lina worked on me to increase my range of motion while helping with the pinched nerve from my arm being in the same position for so long during my surgery. My wife drives a lot for work, and Paul has helped decrease her neck and lower back pain immensely. They are seriously the best therapists I have ever worked with. I would recommend them to anyone who needs anything from stress relief to a medical massage treatment. They are professional, upbeat, easy going, and always on time. And, I love that they meet us where ever we like! We did a staycation recently, where they came to our hotel to give us relaxation massages. Although usually they come to our home, where we focus on pain related issues. We will continue to work with them for a long, long time.</div>
<div class="abs" style="left:0;top:2284px;width:1200px;text-align:center;font-size:13.5px;font-weight:700;color:#222">5/5 stars Massage Therapy</div>
<div class="abs" style="left:552px;top:2316px;width:96px;height:30px;border-radius:15px;border:2px solid #333;background:#f0c23a"></div>

<!-- rates -->
<div class="abs rates"></div>
<div class="abs ring-icon" style="left:562px;top:2439px;width:76px;height:76px;border-width:3px"><svg width="36" height="36" viewBox="0 0 36 36"><circle cx="14" cy="22" r="11" fill="#fff"/><text x="14" y="27" text-anchor="middle" font-family="Lato,sans-serif" font-size="14" font-weight="900" fill="#17c0a6">$</text><path d="M22 14c2-8 8-12 13-12-1 7-5 12-13 12z" fill="#fff"/></svg></div>
<div class="abs" style="left:0;top:2538px;width:1200px;text-align:center;font-size:30px;color:#fff">Our Rates</div>
<div class="abs" style="left:0;top:2589px;width:1200px;text-align:center;font-size:14px;color:#fff">Lorem Ipsum Dolor Sit Amet Ex Vim Quem Primis. Quot Suavitate Mole.</div>
<div class="abs rate-bar">
  <div class="rate"><span class="pair"><svg width="18" height="14" viewBox="0 0 18 14"><path d="M1 2c6 0 10 3 16 10C10 12 5 9 1 2z" fill="#fff"/></svg>$ 75 per</span><span class="pair"><svg width="16" height="16" viewBox="0 0 16 16"><circle cx="8" cy="8" r="6.5" fill="none" stroke="#fff" stroke-width="1.5"/><path d="M8 4v4l3 2" stroke="#fff" stroke-width="1.5" fill="none"/></svg>60 minutes</span></div>
  <div class="rate"><span class="pair"><svg width="18" height="14" viewBox="0 0 18 14"><path d="M1 2c6 0 10 3 16 10C10 12 5 9 1 2z" fill="#fff"/></svg>$ 95 per</span><span class="pair"><svg width="16" height="16" viewBox="0 0 16 16"><circle cx="8" cy="8" r="6.5" fill="none" stroke="#fff" stroke-width="1.5"/><path d="M8 4v4l3 2" stroke="#fff" stroke-width="1.5" fill="none"/></svg>90 minutes</span></div>
  <div class="rate"><span class="pair"><svg width="18" height="14" viewBox="0 0 18 14"><path d="M1 2c6 0 10 3 16 10C10 12 5 9 1 2z" fill="#fff"/></svg>$ 120 per</span><span class="pair"><svg width="16" height="16" viewBox="0 0 16 16"><circle cx="8" cy="8" r="6.5" fill="none" stroke="#fff" stroke-width="1.5"/><path d="M8 4v4l3 2" stroke="#fff" stroke-width="1.5" fill="none"/></svg>120 minutes</span></div>
</div>

<!-- footer wave -->
<svg class="abs" style="left:0;top:2720px" width="1200" height="276" viewBox="0 0 1200 276">
  <path d="M0 120 C300 170 650 160 900 100 C1030 70 1130 70 1200 85 L1200 276 L0 276 Z" fill="#2a2a2a"/>
  <path d="M0 114 C300 164 650 154 900 94 C1030 64 1130 64 1200 79" stroke="#ffffff" stroke-width="6" fill="none" opacity=".85"/>
  <path d="M0 140 C320 180 680 175 920 118 C1040 92 1130 92 1200 104 L1200 276 L0 276 Z" fill="#222"/>
</svg>
<div class="abs footer-logo"><span>Kestrel<br>Way</span></div>
<div class="abs footer-link" style="left:204px">Home</div>
<div class="abs footer-sep" style="left:259px"></div>
<div class="abs footer-link" style="left:393px">Why we stand out?</div>
<div class="abs footer-sep" style="left:517px"></div>
<div class="abs footer-link" style="left:604px">Our Passion</div>
<div class="abs footer-sep" style="left:703px"></div>
<div class="abs footer-link" style="left:789px">Education</div>
<div class="abs footer-sep" style="left:878px"></div>
<div class="abs footer-link" style="left:971px">Contact Us</div>

<div class="abs bottombar"></div>
<div class="abs copyright">© 2016 KESTREL WAY MOBILE MASSAGE &nbsp;|&nbsp; All Rights Reserved</div>
<div class="abs social-dot" style="left:1016px"></div>
<div class="abs social-dot" style="left:1044px"></div>
<div class="abs social-dot" style="left:1080px"></div>

</body>
</html>
```